Ridgeline Journeys business card

please see website
www.ridgelinejourneys.comau

info needed on card
Curtis Halvey
Ph
email
Adventure Riding GPS trails

please use my logo and colours off my site

Curtis Halvey
curtis@ridgelinejourneys.com

```html
<!DOCTYPE html>
<html lang="en">
<head>
<meta charset="utf-8">
<title>Ridgeline Journeys business card</title>
<link href="https://fonts.googleapis.com/css2?family=Oswald:wght@700&family=Arimo:wght@400;700&display=swap" rel="stylesheet">
<style>
  :root {
    --backdrop: #2b2b2b;
    --card-black: #060606;
    --card-white: #ffffff;
    --brand-yellow: #f5d90f;
    --ink: #111111;
    --text-grey: #555555;
    --tagline-light: #e6e6e6;
  }
  * { margin: 0; padding: 0; box-sizing: border-box; }
  html, body { width: 1200px; height: 750px; overflow: hidden; }
  body {
    background: var(--backdrop);
    font-family: "Arimo", Arial, sans-serif;
    position: relative;
  }
  .card {
    position: absolute;
    top: 226px;
    width: 520px;
    height: 297px;
    overflow: hidden;
  }
  .card-back { left: 50px; background: var(--card-black); }
  .card-front { left: 630px; background: var(--card-white); }

  /* back side */
  .back-brand {
    position: absolute;
    left: 0; right: 0; top: 108px;
    text-align: center;
    display: flex; justify-content: center; align-items: center; gap: 12px;
  }
  .brand-mark {
    width: 18px; height: 18px;
    background: var(--brand-yellow);
    border-radius: 50%;
  }
  .back-brand .brand-name {
    font-family: "Oswald", "Arial Narrow", sans-serif;
    font-weight: 700;
    font-size: 34px;
    letter-spacing: 0.5px;
    text-transform: uppercase;
    color: var(--brand-yellow);
  }
  .back-tagline {
    position: absolute;
    left: 0; right: 0; top: 196px;
    text-align: center;
    font-size: 13px;
    color: var(--tagline-light);
  }

  /* front side */
  .front-brand {
    position: absolute;
    left: 160px; top: 62px;
    display: flex; align-items: center; gap: 10px;
  }
  .front-brand .brand-name {
    font-family: "Oswald", "Arial Narrow", sans-serif;
    font-weight: 700;
    font-size: 30px;
    line-height: 1;
    text-transform: uppercase;
    color: var(--ink);
  }
  .name-band {
    position: absolute;
    right: 0; top: 132px;
    width: 196px; height: 46px;
    background: var(--card-black);
    display: flex; align-items: center; justify-content: center;
  }
  .holder-name {
    font-weight: 700;
    font-size: 17px;
    color: var(--brand-yellow);
  }
  .contact-list {
    position: absolute;
    left: 36px; top: 196px;
    list-style: none;
    font-size: 13px;
    color: var(--text-grey);
  }
  .contact-item {
    display: flex; align-items: center; gap: 8px;
    height: 19px;
  }
  .contact-icon { width: 13px; height: 13px; flex: none; }
  .contact-tagline {
    margin-top: 4px;
    font-size: 14px;
    letter-spacing: 0.3px;
  }
</style>
</head>
<body>
  <section class="card card-back" aria-label="Card back">
    <div class="back-brand">
      <span class="brand-mark"></span>
      <span class="brand-name">Ridgeline Journeys</span>
    </div>
    <p class="back-tagline">Adventure Riding GPS trails</p>
  </section>

  <section class="card card-front" aria-label="Card front">
    <div class="front-brand">
      <span class="brand-mark"></span>
      <span class="brand-name">Ridgeline Journeys</span>
    </div>

    <div class="name-band">
      <span class="holder-name">Curtis Halvey</span>
    </div>

    <ul class="contact-list">
      <li class="contact-item">
        <svg class="contact-icon" viewBox="0 0 16 16" aria-hidden="true">
          <path fill="#f5d90f" d="M3 1h3l1.5 4-2 1.3a9 9 0 0 0 4.2 4.2L11 8.5l4 1.5v3a2 2 0 0 1-2 2A12 12 0 0 1 1 3a2 2 0 0 1 2-2z"/>
        </svg>
        <span>555 0142 7781</span>
      </li>
      <li class="contact-item">
        <svg class="contact-icon" viewBox="0 0 16 16" aria-hidden="true">
          <rect x="1" y="3" width="14" height="10" rx="1" fill="#f5d90f"/>
          <path d="M1.5 3.5 8 9l6.5-5.5" fill="none" stroke="#ffffff" stroke-width="1.4"/>
        </svg>
        <span>curtis@ridgelinejourneys.com</span>
      </li>
      <li class="contact-item">
        <svg class="contact-icon" viewBox="0 0 16 16" aria-hidden="true">
          <circle cx="8" cy="8" r="7" fill="#f5d90f"/>
          <path d="M1 8h14M8 1c-3 3.5-3 10.5 0 14M8 1c3 3.5 3 10.5 0 14" fill="none" stroke="#ffffff" stroke-width="1.1"/>
        </svg>
        <span>www.ridgelinejourneys.com.au</span>
      </li>
      <li class="contact-tagline">Adventure Riding GPS trails</li>
    </ul>
  </section>
</body>
</html>
```